MRT Property - Business Cards

Looking for a business card & general letterhead, signage etc design for our new logo.

Colours:
000a20
0056a2
00b5ef
0088ce
68cef2

Fonts:
Poppins
Karla

Please keep look and feel of new brand - example in the zip package I sent.

```html
<!DOCTYPE html>
<html lang="en">
<head>
<meta charset="utf-8">
<title>MRT Property – Business Cards</title>
<link href="https://fonts.googleapis.com/css2?family=Poppins:wght@400;500;600;700&display=swap" rel="stylesheet">
<style>
  :root {
    --stage: #3d3d3d;
    --navy: #0f1428;
    --blue: #0056a2;
    --sky: #00b5ef;
    --mid: #0088ce;
    --light: #68cef2;
    --white: #ffffff;
    --rule: rgba(255,255,255,0.45);
  }
  * { box-sizing: border-box; margin: 0; padding: 0; }
  html, body {
    width: 1200px; height: 803px; overflow: hidden;
    background: var(--stage);
    font-family: "Poppins", Arial, sans-serif;
  }
  .sheet {
    width: 1200px; height: 803px;
    display: flex; align-items: center; justify-content: center; gap: 44px;
  }
  .card {
    width: 520px; height: 297px;
    border-radius: 22px;
    position: relative;
    border-bottom: 3px solid var(--light);
    box-shadow: 0 14px 30px rgba(0,0,0,0.35);
  }
  .card--contact { background: var(--blue); color: var(--white); }
  .card--brand { background: var(--navy); }

  .contact {
    position: absolute; left: 118px; top: 92px;
    display: flex; align-items: stretch;
  }
  .identity {
    display: flex; flex-direction: column; align-items: flex-end;
    justify-content: center; padding-right: 16px;
  }
  .identity__name { font-size: 25px; font-weight: 700; line-height: 1.1; }
  .identity__role { font-size: 12px; font-weight: 400; margin-top: 2px; }
  .divider { width: 1px; background: var(--rule); }
  .details {
    padding-left: 16px; font-size: 12px; line-height: 1.45;
    display: flex; flex-direction: column; justify-content: center;
  }
  .details__address { margin-bottom: 6px; }
  .details__row { display: flex; align-items: center; gap: 7px; }
  .details__row svg { width: 11px; height: 11px; flex: none; }

  .brand {
    position: absolute; left: 50%; top: 50%;
    transform: translate(-50%, -50%);
    display: flex; align-items: center; gap: 14px;
  }
  .brand__dot { width: 34px; height: 34px; border-radius: 50%; background: var(--sky); }
  .brand__name {
    font-size: 40px; font-weight: 700; color: var(--blue);
    letter-spacing: 0.5px; white-space: nowrap;
  }
</style>
</head>
<body>
<main class="sheet">
  <section class="card card--contact" aria-label="Business card, contact side">
    <div class="contact">
      <div class="identity">
        <p class="identity__name">Daniel Reed</p>
        <p class="identity__role">President</p>
      </div>
      <div class="divider"></div>
      <div class="details">
        <p class="details__address">4210 Harbor View Road<br>Westfield, Canada 52810</p>
        <p class="details__row">
          <svg viewBox="0 0 12 12" aria-hidden="true"><path d="M3 1l2 2.5-1.2 1.2c.6 1.3 1.6 2.3 2.9 2.9L7.9 6.4 10.5 8.4 9.4 10.6C5.3 10.3 1.7 6.7 1.4 2.6z" fill="#fff"/></svg>
          555-214-0187
        </p>
        <p class="details__row">
          <svg viewBox="0 0 12 12" aria-hidden="true"><rect x="3" y="0.8" width="6" height="10.4" rx="1" fill="none" stroke="#fff" stroke-width="1.2"/><circle cx="6" cy="9.4" r="0.6" fill="#fff"/></svg>
          555-309-6642
        </p>
        <p class="details__row">
          <svg viewBox="0 0 12 12" aria-hidden="true"><rect x="0.8" y="2.3" width="10.4" height="7.4" fill="#fff"/><path d="M1 2.6l5 4 5-4" fill="none" stroke="#0056a2" stroke-width="1"/></svg>
          info@MRT.com
        </p>
        <p class="details__row">
          <svg viewBox="0 0 12 12" aria-hidden="true"><circle cx="6" cy="6" r="5" fill="none" stroke="#fff" stroke-width="1.1"/><path d="M1 6h10M6 1c-2.4 2.8-2.4 7.2 0 10M6 1c2.4 2.8 2.4 7.2 0 10" fill="none" stroke="#fff" stroke-width="0.9"/></svg>
          www.MRT.com
        </p>
      </div>
    </div>
  </section>

  <section class="card card--brand" aria-label="Business card, brand side">
    <div class="brand">
      <span class="brand__dot" aria-hidden="true"></span>
      <span class="brand__name">MRT Property</span>
    </div>
  </section>
</main>
</body>
</html>
```